Croatia Luxury Cruise Brochure

1) Front page instead of By Journeys of Perla please put by Sea Lantern Voyages – same on the last page where you have her contacts
2) Can you please add into the second page where you have ‘Welcome to your Croatia trip’ itinerary at glance. You can put it just below the text you have. Create a nice looking table .
D1 August 05, 2023 Arrival to Dubrovnik , Welcome cocktail party on Dubrovnik city walls
D2 August 06, 2023 Dubrovnik Highlights city tour – Embark sail to Elafiti
D3 August 07, 2023 Sail to Mljet island and day at leisure at sea
D4 August 08, 2023 Peljesac Wine Tasting with Live Music – Sail to Korcula
D5 August 09, 2023 Korcula Highlights Explorer Tour & Local Estate Dinner
D6 August 10, 2023 Korcula to Vis Island sail
D7 August 11, 2023 Vis Militarty Tour -sail to Pakleni Islands Vetrovo sunset cocktails
D8 August 12, 2023 Hvar island – sail to Split
D9 August 13, 2023 Disembark – Split & Trogir ORTHAV tours with 6-course wine dinner
D10 August 14, 2023 Fly out
Note: All tours & Experiences are optional add ons except the Cocktail reception on Dubrovnik city walls
3) Changes to the itinerary:
D1 is now arrival to Dubrovnik day earlier (AUGU5) and the rest is all moved accordingly. Please check the link
https://portal.bluekeelroutes. com/itinerary/custom-trip-prepared-for-perla-group/
4) Inclusion/Exclusion page we need to update a little. Please make 3 different categories with a note for booking conditions.
Inclusions
• All transfers per itinerary including airport pick up and drop off
• 7 nights cruise on MS Gullwing on half board basis
• All meals stated per itinerary
• Captains dinner
• Unlimited water
• Masseuse on board
• Service of 11 crew members
• Cruise director
• Unlimited WiFi
• Daily cleaning
• Arrival refreshments
• Premium docking
• Usage of non motorized water toys
• Exclusive cocktail reception on Dubrovnik city walls with live music and snacks
Optional Tours
• Dubrovnik Highlights Explorer tour
• Peljesac Wine tour with live music
• Korcula explorer tour with local estate dinner
• Vis Military tour
• Vetrovo Lounge bar reservation (min spend EUR100 per person)
• Split & Trogir ORTHAV Explorer tour
• 6-course farewell dinner with local wine pairing
• 1 night post stay in Belvani 5* hotel in Split (This is added on optional)
Extras
• Tips for the crew
• Beverage consumption
• Usage of motorized water toys – EUR150 per hour
• International flights
• Any personal expenses
Booking conditions
30 % non-refundable deposit needed upon confirmation
Balance of the trip and any optional tours picked are due 06 May, 2023
Luxury travelers from USA and Canada
Tourism

```html
<!DOCTYPE html>
<html lang="en">
<head>
<meta charset="utf-8">
<title>Croatia Luxury Cruise Brochure</title>
<link rel="stylesheet" href="https://fonts.googleapis.com/css2?family=Syncopate:wght@400;700&family=Poppins:wght@300;400;500;600&family=Montserrat:wght@500;600&display=swap">
<style>
  :root{
    --stage:#e7e7e8;
    --paper:#ffffff;
    --blue:#1b8fd8;
    --blue-deep:#0b5aa6;
    --blue-light:#7cc7f0;
    --blue-tint:#eaf5fc;
    --ink:#3a3a3a;
    --ink-soft:#6b6b6b;
    --panel:#3b3b3d;
    --panel-2:#2c2c2e;
  }
  *{box-sizing:border-box;margin:0;padding:0}
  html,body{width:1200px;height:3264px;overflow:hidden}
  body{background:var(--stage);font-family:"Poppins",sans-serif;color:var(--ink);position:relative}
  .row{position:absolute;left:0;width:1200px;height:816px}
  .row + .row{border-top:1px solid #dadadb}
  .spread{position:absolute;left:100px;top:173px;width:1000px;height:470px;display:flex;box-shadow:0 18px 30px rgba(0,0,0,.18)}
  .page{position:relative;width:500px;height:470px;background:var(--paper);overflow:hidden}
  .page.left::after{content:"";position:absolute;right:0;top:0;width:26px;height:100%;background:linear-gradient(90deg,rgba(0,0,0,0),rgba(0,0,0,.14));z-index:4}
  .page.right::before{content:"";position:absolute;left:0;top:0;width:18px;height:100%;background:linear-gradient(90deg,rgba(0,0,0,.12),rgba(0,0,0,0));z-index:4}

  .photo{position:absolute}
  .heading{font-family:"Syncopate",sans-serif;font-weight:400;color:var(--blue);text-transform:uppercase;letter-spacing:.02em;line-height:1.25}
  .body-text{font-size:7.4px;line-height:1.5;color:var(--ink-soft);text-align:justify}
  .body-text p + p{margin-top:6px}

  .folio{position:absolute;bottom:20px;height:14px;display:flex;align-items:center;z-index:3}
  .folio .num{width:13px;height:13px;border-radius:50%;background:var(--blue);color:#fff;font-size:7px;display:flex;align-items:center;justify-content:center;flex:none}
  .folio .rule{height:1px;background:var(--blue);opacity:.7;flex:1}
  .folio.on-left{left:22px;right:22px}
  .folio.on-right{left:22px;right:22px;flex-direction:row-reverse}

  /* covers */
  .back-cover{background:linear-gradient(180deg,#9fd7f6 0%,#3b9be0 18%,#0e5fb1 45%,#0a4f9a 100%)}
  .collage{position:absolute;left:70px;top:40px;width:330px;height:240px}
  .collage .shot{position:absolute;border:4px solid #fff;border-radius:10px;box-shadow:0 4px 10px rgba(0,0,0,.25)}
  .spine-band{position:absolute;right:0;top:0;width:12px;height:100%;background:var(--blue-deep)}
  .contact{position:absolute;left:60px;bottom:70px;color:#fff;font-size:8.5px;letter-spacing:.06em}
  .contact .brand{font-family:"Montserrat",sans-serif;font-weight:600;font-size:11px;letter-spacing:.12em;text-transform:uppercase;margin-bottom:6px}
  .contact .site{font-family:"Montserrat",sans-serif;font-weight:600;letter-spacing:.3em;font-size:9px;margin-bottom:6px}
  .contact .line{display:flex;align-items:center;gap:6px;margin-top:4px}
  .contact svg{width:9px;height:9px;flex:none}
  .back-foot{position:absolute;left:0;bottom:0;width:100%;height:40px;background:#fff}

  .front-cover{background:linear-gradient(180deg,#d9efff 0%,#7fc4f0 14%,#2f8ede 30%,#0b5fb4 60%,#07488f 100%)}
  .cover-title{position:absolute;right:34px;top:40px;font-size:34px;color:var(--blue-deep)}
  .cover-by{position:absolute;right:36px;top:86px;font-family:"Montserrat",sans-serif;font-weight:500;font-size:11px;letter-spacing:.16em;color:var(--blue-deep);text-transform:uppercase}
  .cover-ribbon{position:absolute;left:0;right:0;bottom:56px;height:28px;background:var(--blue);display:flex;justify-content:flex-end;align-items:center;padding:0 28px;color:#fff;font-family:"Montserrat",sans-serif;font-weight:600;font-size:10px;letter-spacing:.14em}
  .cover-foot{position:absolute;left:0;right:0;bottom:0;height:56px;background:#fff;display:flex;align-items:center;justify-content:center;font-family:"Montserrat",sans-serif;font-weight:500;font-size:9.5px;letter-spacing:.24em;color:var(--blue);text-transform:uppercase;white-space:nowrap}

  /* inclusions page */
  .incl-title{position:absolute;left:22px;top:96px;font-size:13px}
  .incl-cols{position:absolute;left:22px;top:124px;width:452px;display:flex;gap:18px}
  .incl-col{flex:1}
  .incl-col h3{font-family:"Montserrat",sans-serif;font-weight:600;font-size:8px;letter-spacing:.12em;color:#fff;background:var(--blue);text-transform:uppercase;padding:3px 7px;margin-bottom:5px}
  .incl-col h3.next{margin-top:8px}
  .incl-col ul{list-style:none}
  .incl-col li{font-size:6.8px;line-height:1.4;color:var(--ink-soft);padding-left:9px;position:relative;margin-bottom:1.5px}
  .incl-col li::before{content:"";position:absolute;left:1px;top:3px;width:4px;height:4px;border-radius:50%;background:var(--blue)}
  .booking{position:absolute;left:22px;top:366px;width:452px;background:linear-gradient(180deg,var(--panel),var(--panel-2));color:#fff;font-size:7px;line-height:1.5}
  .booking .date{background:var(--blue);font-weight:600;font-size:7.6px;padding:4px 10px;text-transform:uppercase;letter-spacing:.04em}
  .booking ul{list-style:none;padding:6px 10px 7px}
  .booking li b{color:var(--blue-light);font-weight:600}

  /* about + itinerary */
  .about-copy{position:absolute;left:140px;top:0;width:360px;height:100%;background:#fff;padding:26px 22px 0 22px}
  .about-copy .heading{font-size:13px;margin-bottom:10px}
  .about-copy .body-text{font-size:6.9px;line-height:1.45}
  .glance-title{font-family:"Montserrat",sans-serif;font-weight:600;font-size:8px;letter-spacing:.14em;color:var(--blue-deep);text-transform:uppercase;margin:12px 0 5px}
  .glance{width:100%;border-collapse:collapse;font-size:6.5px;line-height:1.3;color:var(--ink)}
  .glance th{background:var(--blue);color:#fff;font-weight:600;text-transform:uppercase;letter-spacing:.06em;text-align:left;padding:3px 5px;font-size:6.5px}
  .glance td{padding:2.6px 5px;border-bottom:1px solid #d8e9f5;vertical-align:top}
  .glance tr:nth-child(even) td{background:var(--blue-tint)}
  .glance td.day{color:var(--blue);font-weight:600;width:24px}
  .glance td.when{white-space:nowrap;width:78px}
  .glance-note{font-size:6.4px;color:var(--ink-soft);margin-top:5px;font-style:italic}

  /* day pages */
  .day-tag{position:absolute;background:var(--blue);color:#fff;font-family:"Syncopate",sans-serif;font-size:15px;letter-spacing:.04em;display:flex;align-items:center;justify-content:center;z-index:2}
  .day-tag.vertical{writing-mode:vertical-rl;transform:rotate(180deg)}
  .info-box{position:absolute;background:linear-gradient(180deg,var(--panel),var(--panel-2));color:#fff;font-size:7.4px;line-height:1.45}
  .info-box .date{background:var(--blue);font-weight:600;font-size:7.6px;padding:6px 10px;text-transform:uppercase}
  .info-box .label{color:var(--blue-light);font-weight:600;text-transform:uppercase;font-size:7.2px}
  .info-box .val{text-transform:uppercase}
  .info-box.wide .grid{display:flex;gap:22px;padding:8px 10px}
  .info-box.tall .stack{padding:10px 12px}
  .info-box.tall .stack .label{margin-top:10px}
  .info-box .pair{padding:4px 10px 0 10px;text-transform:uppercase}
  .info-box .pair b{color:var(--blue-light);font-weight:600}
</style>
</head>
<body>

<!-- Row 1: covers -->
<section class="row" style="top:0">
  <div class="spread">
    <div class="page left back-cover">
      <div class="collage">
        <div class="shot" role="img" aria-label="Photo of jet ski riders on the sea" style="left:0;top:70px;width:110px;height:80px;background:linear-gradient(135deg,#1f3a2a,#3e6d3f 50%,#0f2b48);transform:rotate(-8deg)"></div>
        <div class="shot" role="img" aria-label="Photo of a guest relaxing on the yacht deck" style="left:110px;top:40px;width:120px;height:120px;background:linear-gradient(160deg,#f1ede6,#c9b9a4 50%,#6d8fb0);transform:rotate(-6deg)"></div>
        <div class="shot" role="img" aria-label="Photo of sun loungers on the yacht deck" style="left:225px;top:0;width:100px;height:82px;background:linear-gradient(140deg,#d9cdbb,#8e7b69 55%,#3b5f82);transform:rotate(-10deg)"></div>
        <div class="shot" role="img" aria-label="Photo of the mini cruiser at anchor" style="left:235px;top:92px;width:95px;height:62px;background:linear-gradient(150deg,#cfe4f3,#7aa8cf 60%,#2f6aa3);transform:rotate(-8deg)"></div>
        <div class="shot" role="img" aria-label="Photo of dining on the yacht" style="left:65px;top:160px;width:120px;height:72px;background:linear-gradient(140deg,#e9e4de,#a59a8e 50%,#4b4744);transform:rotate(-8deg)"></div>
      </div>
      <div class="contact">
        <div class="brand">Sea Lantern Voyages</div>
        <div class="site">WWW.BLUEKEELROUTES.COM</div>
        <div class="line">18 Harbourline Road, Portwell, 22140</div>
        <div class="line">
          <svg viewBox="0 0 10 10"><path d="M2 1 L4 1 L5 3 L4 4 Q5 6 6 6 L7 5 L9 6 L9 8 Q8 9 7 9 Q1 8 1 2 Q1 1 2 1Z" fill="#fff"/></svg>
          555-210-4418 &nbsp;·&nbsp; 555-210-4467 &nbsp;·&nbsp; 555-210-4490
        </div>
        <div class="line">
          <svg viewBox="0 0 10 10"><rect x="1" y="2" width="8" height="6" fill="none" stroke="#fff" stroke-width="1"/><path d="M1 2 L5 5.5 L9 2" fill="none" stroke="#fff" stroke-width="1"/></svg>
          hello@bluekeelroutes.com
        </div>
      </div>
      <div class="back-foot"></div>
      <div class="spine-band"></div>
    </div>
    <div class="page right front-cover" role="img" aria-label="Aerial photo of a luxury mini cruiser sailing on deep blue sea">
      <div class="cover-title heading">Croatia</div>
      <div class="cover-by">by Sea Lantern Voyages</div>
      <div class="cover-ribbon"><span>05 AUGUST - 14 AUGUST, 2023</span></div>
      <div class="cover-foot">Luxury explorer cruise on Gullwing mini cruiser</div>
    </div>
  </div>
</section>

<!-- Row 2: inclusions + about with itinerary -->
<section class="row" style="top:816px">
  <div class="spread">
    <div class="page left">
      <div class="photo" role="img" aria-label="Aerial photo of a forested rocky coastline meeting turquoise water" style="left:0;top:0;width:100%;height:80px;background:linear-gradient(90deg,#4d5a2c 0%,#6f8a2e 28%,#3f6a35 52%,#6f8690 62%,#1d6b82 75%,#0f5a77 100%)"></div>
      <h2 class="heading incl-title">Inclusions &amp; Extras</h2>
      <div class="incl-cols">
        <div class="incl-col">
          <h3>Inclusions</h3>
          <ul>
            <li>All transfers per itinerary including airport pick up and drop off</li>
            <li>7 nights cruise on MS Gullwing on half board basis</li>
            <li>All meals stated per itinerary</li>
            <li>Captains dinner</li>
            <li>Unlimited water</li>
            <li>Masseuse on board</li>
            <li>Service of 11 crew members</li>
            <li>Cruise director</li>
            <li>Unlimited WiFi</li>
            <li>Daily cleaning</li>
            <li>Arrival refreshments</li>
            <li>Premium docking</li>
            <li>Usage of non motorized water toys</li>
            <li>Exclusive cocktail reception on Dubrovnik city walls with live music and snacks</li>
          </ul>
        </div>
        <div class="incl-col">
          <h3>Optional Tours</h3>
          <ul>
            <li>Dubrovnik Highlights Explorer tour</li>
            <li>Peljesac Wine tour with live music</li>
            <li>Korcula explorer tour with local estate dinner</li>
            <li>Vis Military tour</li>
            <li>Vetrovo Lounge bar reservation (min spend EUR100 per person)</li>
            <li>Split &amp; Trogir ORTHAV Explorer tour</li>
            <li>6-course farewell dinner with local wine pairing</li>
            <li>1 night post stay in Belvani 5* hotel in Split (This is added on optional)</li>
          </ul>
          <h3 class="next">Extras</h3>
          <ul>
            <li>Tips for the crew</li>
            <li>Beverage consumption</li>
            <li>Usage of motorized water toys – EUR150 per hour</li>
            <li>International flights</li>
            <li>Any personal expenses</li>
          </ul>
        </div>
      </div>
      <div class="booking">
        <div class="date">Booking conditions</div>
        <ul>
          <li><b>Deposit :</b> 30 % non-refundable deposit needed upon confirmation</li>
          <li><b>Balance :</b> Balance of the trip and any optional tours picked are due 06 May, 2023</li>
        </ul>
      </div>
      <div class="folio on-left"><span class="num">1</span><span class="rule"></span></div>
    </div>
    <div class="page right">
      <div class="photo" role="img" aria-label="Aerial photo of a boat cruising along a green coastline" style="left:0;top:0;width:140px;height:100%;background:linear-gradient(110deg,#1b5f6e 0%,#2a8196 45%,#3b99a9 60%,#4d7a55 85%,#6a8d44 100%)"></div>
      <div class="about-copy">
        <h2 class="heading">About Croatia</h2>
        <div class="body-text">
          <p>The Croatian Coast is the premiere setting for the ultimate island hopping experience. The Dalmatian Islands in Croatia are among the most famous in the Mediterranean region. Wild, rugged, and hiding a thousand-year history, many are protected as national park and offer a varied and diverse cruising ground for an yacht charter. The cruising is splendid, encompassing long and short passages to charming anchorages amid rocky islets, ancient villages steeped in history, and translucent waters.</p>
          <p>In total Croatia has over 1200 islands and islets to explore and visit so depending on your travel preference and travel style the combinations of itineraries are endless. Enjoy your cruise on mini cruiser Gullwing by visiting highlights of Adriatic coastline.</p>
        </div>
        <div class="glance-title">Itinerary at a glance</div>
        <table class="glance">
          <thead><tr><th>Day</th><th>Date</th><th>Programme</th></tr></thead>
          <tbody>
            <tr><td class="day">D1</td><td class="when">August 05, 2023</td><td>Arrival to Dubrovnik, welcome cocktail party on Dubrovnik city walls</td></tr>
            <tr><td class="day">D2</td><td class="when">August 06, 2023</td><td>Dubrovnik Highlights city tour – embark, sail to Elafiti</td></tr>
            <tr><td class="day">D3</td><td class="when">August 07, 2023</td><td>Sail to Mljet island and day at leisure at sea</td></tr>
            <tr><td class="day">D4</td><td class="when">August 08, 2023</td><td>Peljesac Wine Tasting with Live Music – sail to Korcula</td></tr>
            <tr><td class="day">D5</td><td class="when">August 09, 2023</td><td>Korcula Highlights Explorer Tour &amp; Local Estate Dinner</td></tr>
            <tr><td class="day">D6</td><td class="when">August 10, 2023</td><td>Korcula to Vis Island sail</td></tr>
            <tr><td class="day">D7</td><td class="when">August 11, 2023</td><td>Vis Military Tour – sail to Pakleni Islands, Vetrovo sunset cocktails</td></tr>
            <tr><td class="day">D8</td><td class="when">August 12, 2023</td><td>Hvar island – sail to Split</td></tr>
            <tr><td class="day">D9</td><td class="when">August 13, 2023</td><td>Disembark – Split &amp; Trogir ORTHAV tours with 6-course wine dinner</td></tr>
            <tr><td class="day">D10</td><td class="when">August 14, 2023</td><td>Fly out</td></tr>
          </tbody>
        </table>
        <p class="glance-note">Note: All tours &amp; experiences are optional add ons except the cocktail reception on Dubrovnik city walls.</p>
      </div>
      <div class="folio on-right"><span class="num">2</span><span class="rule" style="margin-left:180px"></span></div>
    </div>
  </div>
</section>

<!-- Row 3: days 1–2 -->
<section class="row" style="top:1632px">
  <div class="spread">
    <div class="page left">
      <div class="photo" role="img" aria-label="Photo of an old stone chapel on a cliff under a bright sky" style="left:0;top:0;width:100%;height:212px;background:linear-gradient(90deg,#cfe0ec 0%,#b7cfe0 30%,#a79a83 55%,#8d7a60 75%,#6f6a58 100%)"></div>
      <div class="day-tag" style="left:22px;top:190px;width:72px;height:26px">DAY 1</div>
      <h2 class="heading" style="position:absolute;left:22px;top:232px;font-size:11px">Arrival to Dubrovnik<br>&amp; Welcome Dinner</h2>
      <div class="body-text" style="position:absolute;left:22px;top:272px;width:298px">
        <p>Welcome to Dubrovnik – the pearl of the Adriatic! Dubrovnik lies in the extreme south of Croatia, basking in glorious Mediterranean sunshine for much of the year. A fairytale city of beautiful Baroque, Gothic and Renaissance churches, aristocratic palaces, red-roofed townhouses, magnificent monasteries and fascinating history. Dubrovnik's old town is known as one of the world's finest and most perfectly preserved medieval cities. One of the best views in the world is to be had from its monumental City Walls – be prepared to be amazed!</p>
        <p>Upon arrival, meet your new friends and the crew during welcome reception and dinner on board.</p>
      </div>
      <div class="info-box tall" style="left:340px;top:236px;width:138px;height:150px">
        <div class="date">August 5, 2023<br>Arrival to Dubrovnik</div>
        <div class="stack">
          <div class="label" style="margin-top:0">Accommodation</div>
          <div>Mini cruiser Gullwing</div>
          <div class="label">Meals</div>
          <div>Dinner on board, snack</div>
        </div>
      </div>
      <div class="folio on-left"><span class="num">3</span><span class="rule"></span></div>
    </div>
    <div class="page right">
      <h2 class="heading" style="position:absolute;left:22px;top:22px;width:260px;font-size:12.5px">Dubrovnik City Explorer Tour &amp; Wine Event with Live Local Music</h2>
      <div class="body-text" style="position:absolute;left:22px;top:88px;width:252px">
        <p>After breakfast it is the time to explore the wonders of Dubrovnik's old town, a ORTHAV World Heritage Site and one of the most important living historical monuments in this part of Europe. Your local guide will show you this magical medieval town full of legends and give you a glimpse into the incredible history that makes Dubrovnik such a unique city. Explore Dubrovnik's famed City Walls and enjoy a unique view of the Old Town from above, including its narrow streets and small squares. Today Dubrovnik is one of the most beautiful towns in the Mediterranean and you will see why. Dubrovnik used to be an independent republic, surviving mostly on trade. The whole city is alive with tourists and locals who wander the centuries-old streets admiring the architecture. After the city tour, we will have a private wine event in one of the wine cellars within the old town of Dubrovnik. Enjoy local wines accompanied with live music. After the private event, free time in Dubrovnik to enjoy the city on your own before another dinner on board prepared by our chef on board of Gullwing.</p>
      </div>
      <div class="info-box wide" style="left:22px;top:330px;width:252px;height:66px">
        <div class="date">August 6, 2023 &nbsp;Dubrovnik walking tour</div>
        <div class="grid">
          <div><div class="label">Accommodation</div><div class="val">Mini cruiser Gullwing</div></div>
          <div><div class="label">Meals</div><div class="val">Breakfast on board,<br>dinner on board, snack</div></div>
        </div>
      </div>
      <div class="photo" role="img" aria-label="Photo of friends raising glasses of red wine at a dinner table" style="left:292px;top:0;width:208px;height:100%;background:linear-gradient(160deg,#4a3a30 0%,#7a5a45 35%,#a88770 55%,#5c4636 80%,#2f2622 100%)"></div>
      <div class="day-tag vertical" style="left:272px;top:330px;width:24px;height:70px">DAY 2</div>
      <div class="folio on-right" style="left:300px"><span class="num">4</span></div>
    </div>
  </div>
</section>

<!-- Row 4: days 3–4 -->
<section class="row" style="top:2448px">
  <div class="spread">
    <div class="page left">
      <h2 class="heading" style="position:absolute;left:22px;top:20px;width:240px;font-size:10.5px">Dubrovnik to National Park Mljet with Captains Dinner on Board</h2>
      <div class="body-text" style="position:absolute;left:22px;top:70px;width:244px">
        <p>During breakfast we'll start cruising to Mljet island. We will be passing some of the most secluded islands on the Adriatic where we shall stop for a swim. Before arriving to National Park Mljet we'll enjoy lunch on board.</p>
        <p>The Mljet National Park is the oldest marine protected area in the Mediterranean and it has delighted its numerous visitors for decades with the colours and the scent of untouched nature. The park stretches over almost 5300 hectares, including a marine area of 500 meters from the coast, islands and cliffs, and therefore spans over almost a third of the island. Two deep bays filled with seawater, known as Small Lake and Great Lake, are the most famous locations of this area and an important geological and oceanographical phenomenon. The entire surface area of the park is extremely rich with life, and numerous endemic and endangered species are a testament of the importance of protecting it. The Benedictine monastery located at one of the most beautiful locations in these areas, on the island of St. Mary, is also the most visited location.</p>
        <p>After we explore the natural beauty of Mljet, we shall have captain's dinner on the boat where the captain and the crew prepare the real feast on board of Gullwing.</p>
      </div>
      <div class="info-box" style="left:22px;top:356px;width:244px;height:66px">
        <div class="date">August 7, 2023 NP Mljet walking tour</div>
        <div class="pair"><b>Accommodation :</b> Mini cruiser Gullwing</div>
        <div class="pair"><b>Meals :</b> Breakfast on board, lunch on board, dinner on board</div>
      </div>
      <div class="photo" role="img" aria-label="Photo of a stone hermitage built into a rocky cliff" style="left:282px;top:0;width:218px;height:100%;background:linear-gradient(170deg,#b49c7c 0%,#8e7658 40%,#6f5d45 70%,#8b7c66 100%)"></div>
      <div class="day-tag vertical" style="left:262px;top:340px;width:24px;height:82px">DAY 3</div>
      <div class="folio on-left" style="right:260px"><span class="num">5</span></div>
    </div>
    <div class="page right">
      <div class="photo" role="img" aria-label="Photo of a walled old town with red roofs by the sea" style="inset:0;background:linear-gradient(180deg,#c7d6e2 0%,#b9c9d6 40%,#a36e52 62%,#7d6654 75%,#3f6f8c 100%)"></div>
      <div style="position:absolute;left:210px;top:0;width:290px;height:100%;background:rgba(255,255,255,.9)"></div>
      <h2 class="heading" style="position:absolute;left:226px;top:20px;width:260px;font-size:10.5px">Mljet Korcula Island Explorer Tour &amp; Local Farm to Table Dinner with Live Music</h2>
      <div class="body-text" style="position:absolute;left:226px;top:70px;width:254px">
        <p>Today we continue cruising to Korčula island and shall arrive to there right after the lunch on board.</p>
        <p>Korčula is considered one of the most charming towns of the Adriatic, and history and tradition are apparent when you walk along Korčula streets and squares. You'll get a superb insight into the history of Korčula from your local guide and we promise you that you might want to move here forever. This town sightseeing private tour includes a visit to the cultural and historical monuments of Korčula Old Town: St Mark's Cathedral and other churches in the Old Town, the Bishop's Treasury, the Town Museum, the Icon Museum, as well as other interesting places. Korčula is a town of secrets and if you scratch the surface, get into its hidden courtyards, backstreets and tucked-away alleyways, you'll soon discover that there is much more to Korčula than the well-known tourist spots.</p>
        <p>In the evening we are visiting another hidden gem of the Adriatic. We will be transferred to local farm for traditional dinner with live music. The chef here is a true character and local from Korčula and the farm is completely family owned, serving only food made out of the best local ingredients. Enjoy the night before we return back on board of Gullwing.</p>
      </div>
      <div class="info-box" style="left:226px;top:356px;width:254px;height:66px">
        <div class="date">August 8, 2023 &nbsp;Sightseeing Korčula tour</div>
        <div class="pair"><b>Accommodation :</b> Mini cruiser Gullwing</div>
        <div class="pair"><b>Meals :</b> Dinner, breakfast on board, lunch on board</div>
      </div>
      <div class="day-tag vertical" style="left:186px;top:340px;width:24px;height:82px">DAY 4</div>
      <div class="folio on-right" style="left:226px"><span class="num">6</span><span class="rule"></span></div>
    </div>
  </div>
</section>

</body>
</html>
```